Letterhead for a German Distribution/Manufacturing Company

We need a professional Letterhead in a unique Design.
not to playful.
The Letterhead has to show show that we are a international company with headquater in Germany.
all details like adress, Vat Tax Number, Bank Accout, Eori, email, Company number has to be on the Letterhead.
for example use: VAT TAX DE5470318 Bank Account: Kestrel Bank IBAN DE412058731ß204683 Swift: MORV0417352 EORI 3150428697 Company Number: HRB 51806 Adress: VOLMINTA UG Ahornweg 7 Postal Code 06384 City Morlitz Country: Germany Email: info@volminta-example.com
the design can be colored but doesnt have to be
Industry/Entity Type
Manufacturing and international distribution
Requirements
Must have
- show that we are a international company with headquater in Germany. our company infos and logo

```html
<!DOCTYPE html>
<html lang="en">
<head>
<meta charset="utf-8">
<title>VOLMINTA Letterhead</title>
<link href="https://fonts.googleapis.com/css2?family=Arimo:wght@400;700&family=Mulish:wght@600;700&display=swap" rel="stylesheet">
<style>
  :root {
    --backdrop: #cbc9ca;
    --paper: #ffffff;
    --ink: #4a4a4a;
    --ink-soft: #555555;
    --band: #4a4a4a;
    --on-band: #ffffff;
  }
  * { box-sizing: border-box; margin: 0; padding: 0; }
  html, body {
    width: 1173px; height: 1200px; overflow: hidden;
    background: var(--backdrop);
  }
  .letterhead {
    position: absolute; left: 230px; top: 96px;
    width: 714px; height: 1009px;
    background: var(--paper);
    color: var(--ink);
    font-family: "Arimo", Arial, sans-serif;
  }
  .masthead {
    height: 118px; background: var(--band);
    display: flex; align-items: center; justify-content: center; gap: 12px;
  }
  .brand-dot {
    width: 34px; height: 34px; border-radius: 50%;
    background: var(--on-band);
  }
  .brand-name {
    font-family: "Mulish", sans-serif; font-weight: 600;
    font-size: 40px; letter-spacing: 1px; color: var(--on-band);
  }
  .salutation {
    position: absolute; left: 66px; top: 310px;
    font-family: "Mulish", sans-serif; font-weight: 700;
    font-size: 16px; color: var(--ink-soft);
  }
  .letter-body {
    position: absolute; left: 64px; top: 357px;
    font-size: 12.2px; line-height: 14.7px; color: var(--ink-soft);
  }
  .letter-body p + p { margin-top: 13px; }
  .letter-body .line { display: block; white-space: nowrap; }
  .closing {
    position: absolute; left: 65px; top: 659px;
    font-family: "Mulish", sans-serif; font-weight: 700;
    font-size: 9.5px; color: var(--ink);
  }
  .signature {
    position: absolute; left: 65px; top: 702px;
    width: 118px; height: 36px;
    background: linear-gradient(90deg, #e2e2e2, #f1f1f1);
    border-radius: 4px;
  }
  .footer {
    position: absolute; left: 0; right: 0; top: 947px; height: 44px;
    font-size: 11.2px; line-height: 14.2px; color: var(--ink);
    white-space: nowrap;
  }
  .footer-col { position: absolute; top: 0; }
  .footer-col b { font-weight: 700; }
  .col-tax { left: 32px; }
  .col-registry { left: 233px; }
  .col-contact { left: 434px; }
  .col-address { left: 625px; }
  .footer-divider { position: absolute; top: 1px; width: 1px; height: 42px; background: var(--ink); }
  .divider-a { left: 216px; }
  .divider-b { left: 418px; }
  .divider-c { left: 612px; }
  .contact-line { display: flex; align-items: center; gap: 6px; }
  .contact-line svg { width: 9px; height: 9px; fill: var(--ink); flex: none; }
</style>
</head>
<body>
<main class="letterhead">
  <header class="masthead">
    <span class="brand-dot"></span>
    <span class="brand-name">VOLMINTA</span>
  </header>

  <h1 class="salutation">Dear Mr. Brandt,</h1>

  <section class="letter-body">
    <p>
      <span class="line">Lorem ipsum dolor sit amet, consectetuer adipiscing elit, sed diam nonmmy nibh euismod tincidunt ut laor</span>
      <span class="line">eet dolore magna aliquam erat volutpat. Ut wisi enim ad minim veniam, quis nostrud exerci tationmcorper</span>
      <span class="line">suscipit lobortis nisl ut aliquip ex ea commodo consequat. Duis autem vel eum iriure dolor in hendrerit in</span>
      <span class="line">vulputate velit esse molestie consequat, vel illum dolore eu feugiat</span>
    </p>
    <p>
      <span class="line">Rorem ipsum dolor sit amet, consectetuer adipiscing elit, sed diam nonmmy nibh euismod tincidunt ut laor</span>
      <span class="line">eet dolore magna aliquam erat volutpat. Ut wisi enim ad minim veniam, quis nostrud exerci tationmcorper</span>
      <span class="line">suscipit lobortis nisl ut aliquip ex ea commodo consequat. Duis autem vel eum iriure dolor in hendrerit in</span>
      <span class="line">vulputate velit esse molest</span>
    </p>
    <p>
      <span class="line">Dorem ipsum dolor sit amet, consectetuer adipiscing elit, sed diam nonmmy nibh euismod tincidunt ut laor</span>
      <span class="line">eet dolore magna aliquam erat volutpat. Ut wisi enim ad minim veniam, quis nostrud exerci tationmcorper</span>
      <span class="line">suscipit lobortis nisl ut aliquip ex ea commodo consequat. Duis autem vel eum iriure dolor in hendrerit in</span>
      <span class="line">suscipit lobortis nisl ut aliquip ex ea commodo consequat. Duis autem vel eum iriure dolor in hendrerit in</span>
      <span class="line">vulputate velit esse molestie consequat, vel illum</span>
    </p>
    <p>
      <span class="line">Sorem ipsum dolor sit amet, consectetuer adipiscing elit, sed diam nonmmy nibh euismod tincidunt ut laor</span>
      <span class="line">eet dolore magna aliquam erat volutpat. Ut wisi enim ad minim veniam, quis nostrud exerci tationmcorper</span>
      <span class="line">suscipit lobortis nisl ut aliquip ex ea commodo consequat. Duis autem vel eum iriure dolor in</span>
    </p>
  </section>

  <p class="closing">Sincerely,</p>
  <div class="signature" role="img" aria-label="Handwritten signature of the sender"></div>

  <footer class="footer">
    <div class="footer-col col-tax">
      <div><b>VAT TAX</b> DE5470318</div>
      <div><b>Bank Account:</b> Kestrel Bank</div>
      <div><b>IBAN</b> DE412058731ß204683</div>
    </div>
    <span class="footer-divider divider-a"></span>
    <div class="footer-col col-registry">
      <div><b>Swift:</b> MORV0417352</div>
      <div><b>EORI</b> 3150428697</div>
      <div><b>Company Number:</b> HRB 51806</div>
    </div>
    <span class="footer-divider divider-b"></span>
    <div class="footer-col col-contact">
      <div class="contact-line">
        <svg viewBox="0 0 10 10" aria-hidden="true"><path d="M2 0.5 L3.6 2.6 L2.8 3.6 Q4 6 6.4 7.2 L7.4 6.4 L9.5 8 L8.2 9.5 Q3 9 0.5 1.8 Z"/></svg>
        <span>555-201-4836</span>
      </div>
      <div class="contact-line">
        <svg viewBox="0 0 10 10" aria-hidden="true"><path d="M0.5 2 H9.5 V8 H0.5 Z M1.2 2.6 L5 5.4 L8.8 2.6" fill="none" stroke="#4a4a4a" stroke-width="1.1"/></svg>
        <span>info@volminta-example.com</span>
      </div>
      <div class="contact-line">
        <svg viewBox="0 0 10 10" aria-hidden="true"><circle cx="5" cy="5" r="4.3" fill="none" stroke="#4a4a4a" stroke-width="1.1"/><path d="M0.8 5 H9.2 M5 0.7 Q2.4 5 5 9.3 Q7.6 5 5 0.7" fill="none" stroke="#4a4a4a" stroke-width="0.9"/></svg>
        <span>www.volminta-example.com</span>
      </div>
    </div>
    <span class="footer-divider divider-c"></span>
    <div class="footer-col col-address">
      <div>Ahornweg 7</div>
      <div>06384, Morlitz</div>
      <div>Germany</div>
    </div>
  </footer>
</main>
</body>
</html>
```